Designer Instructions – Updated Referral Program Flyer

(Based on the mock-up in “Brief Layout and Instructions.pdf”)

OVERALL STYLE + LAYOUT

Maintain the same general layout, structure, and flow as the mock-up flyer (front and back).

This is an update of an older flyer, not a full redesign — keep the same sections, proportions, and overall visual feel, but with cleaner, more modern design improvements.

The final flyer should look clean, bold, professional, and high-impact, geared toward realtors, property managers, and contractors who refer work.

FRONT SIDE INSTRUCTIONS
1. Header Section

Remove the Rebuild Harbor Crest logo from the top banner.
(Shown on page 1 of the PDF)

2. Main Headline

Keep the same three-line structure:
EARN
UNLIMITED
CASH

Center it, maximize impact, and increase the font size of CASH so all three words match in importance.

Make the headline bold, clean, and the main focal point.

3. Cash Incentive Box

Keep the "$500 minimum OR 10% per referral" box, but upgrade the graphics to look sharper and more modern.

Ensure the wording matches exactly what’s in the mock-up.

4. Premier Partner Program Ribbon

Clean up and modernize the "PREMIER PARTNER PROGRAM" bar while keeping the same position and structure.

Ensure the checkmark badge remains crisp and professional.

5. Supporting Icons Section

Keep the four icons/benefit boxes (Guaranteed Payout, Free Evaluations, Affordable Solutions, Industry Leaders) in the same order.

Update the icons to cleaner, more modern styles — but maintain the same meanings.

Improve alignment and spacing for sharper visual consistency.

6. Remove Icons in Contact Area

At the bottom (“CALL TEXT OR BOOK ONLINE 858-471-6093 BrightlaneRenovate.com”), remove the phone and internet icons, as noted on page 2 of the PDF.

7. Replace All Images

I (Dorian) will provide all updated stock images separately via email.

Replace the flood/water-damage imagery and roof leak with the new images I send.

Keep image placement and proportions the same as the mock-up.

BACK SIDE INSTRUCTIONS
1. Header Image + “REFER / EARN” Section

Maintain the same large split-image layout (“The more you refer, the more you earn”).

Replace all background imagery with the new assets I will send.

Keep the CASH FLOW image section but modernize the type and spacing.

2. “HOW IT WORKS” Section

Preserve the three-column layout:

Refer Flood, Water & Mold Damage

We Take Care of Everything (evaluations/insurance)

Get Paid to Share

Update images, tighten spacing, and use modern iconography.

3. Remove Phone/Internet Icons

Same as the front side — remove small communication icons and keep only the text/number/URL.

4. Bottom Contact Bar

Keep the blue bar, same wording, same layout — just modernize the style if needed for clarity.

5. Replace All Back-Side Images

Again, I will email you the image assets.

Keep the layout EXACT — just update with higher-quality photos and improved design.

TEXT CONTENT (Keep as-is unless spacing adjustments needed)

All text shown in the PDF should remain exactly the same unless spacing or visual balance requires minor adjustments.
Example from page 3:

“REFER FLOOD, MOLD & CONSTRUCTION JOBS”

“We Schedule a Free Estimate. If Approved, You Get Paid.”

“Everybody Benefits From Referrals”

Everything stays, just refreshed and visually improved.

DESIGN GOALS

Flyer should look high-end and trustworthy, not salesy.

Consistent color theme: blues, whites, yellows, same palette as original.

Use bold, modern fonts with strong readability.

Ensure all headlines pop and all benefit boxes are clean, well-aligned, and evenly spaced.

The final result should feel like a premium referral program flyer for a top-tier restoration/remodel company.

FILES I WILL PROVIDE

I will send the designer:

All replacement stock photos

Any updated logos (if needed)

Original high-resolution version of the mock-up (if available)

Any additional icons preferred

Colors
0054AA
0677BA
7BADD7
CADEEF
E8F1F8

Requirements
Must have
• Designer Instructions – Updated Referral Program Flyer (Based on the mock-up in “Brief Layout and Instructions.pdf”) OVERALL STYLE + LAYOUT Maintain the same general layout, structure, and flow as the mock-up flyer (front and back). This is an update of an older flyer, not a full redesign — keep the same sections, proportions, and overall visual feel, but with cleaner, more modern design improvements. The final flyer should look clean, bold, professional, and high-impact, geared toward realtors, property managers, and contractors who refer work. FRONT SIDE INSTRUCTIONS 1. Header Section Remove the Rebuild Harbor Crest logo from the top banner. (Shown on page 1 of the PDF) 2. Main Headline Keep the same three-line structure: EARN UNLIMITED CASH Center it, maximize impact, and increase the font size of CASH so all three words match in importance. Make the headline bold, clean, and the main focal point. 3. Cash Incentive Box Keep the "$500 minimum OR 10% per referral" box, but upgrade the graphics to look sharper and more modern. Ensure the wording matches exactly what’s in the mock-up. 4. Premier Partner Program Ribbon Clean up and modernize the "PREMIER PARTNER PROGRAM" bar while keeping the same position and structure. Ensure the checkmark badge remains crisp and professional. 5. Supporting Icons Section Keep the four icons/benefit boxes (Guaranteed Payout, Free Evaluations, Affordable Solutions, Industry Leaders) in the same order. Update the icons to cleaner, more modern styles — but maintain the same meanings. Improve alignment and spacing for sharper visual consistency. 6. Remove Icons in Contact Area At the bottom (“CALL TEXT OR BOOK ONLINE 858-471-6093 BrightlaneRenovate.com”), remove the phone and internet icons, as noted on page 2 of the PDF. 7. Replace All Images I (Dorian) will provide all updated stock images separately via email. Replace the flood/water-damage imagery and roof leak with the new images I send. Keep image placement and proportions the same as the mock-up. BACK SIDE INSTRUCTIONS 1. Header Image + “REFER / EARN” Section Maintain the same large split-image layout (“The more you refer, the more you earn”). Replace all background imagery with the new assets I will send. Keep the CASH FLOW image section but modernize the type and spacing. 2. “HOW IT WORKS” Section Preserve the three-column layout: Refer Flood, Water & Mold Damage We Take Care of Everything (evaluations/insurance) Get Paid to Share Update images, tighten spacing, and use modern iconography. 3. Remove Phone/Internet Icons Same as the front side — remove small communication icons and keep only the text/number/URL. 4. Bottom Contact Bar Keep the blue bar, same wording, same layout — just modernize the style if needed for clarity. 5. Replace All Back-Side Images Again, I will email you the image assets. Keep the layout EXACT — just update with higher-quality photos and improved design. TEXT CONTENT (Keep as-is unless spacing adjustments needed) All text shown in the PDF should remain exactly the same unless spacing or visual balance requires minor adjustments. Example from page 3: “REFER FLOOD, MOLD & CONSTRUCTION JOBS” “We Schedule a Free Estimate. If Approved, You Get Paid.” “Everybody Benefits From Referrals” Everything stays, just refreshed and visually improved. DESIGN GOALS Flyer should look high-end and trustworthy, not salesy. Consistent color theme: blues, whites, yellows, same palette as original. Use bold, modern fonts with strong readability. Ensure all headlines pop and all benefit boxes are clean, well-aligned, and evenly spaced. The final result should feel like a premium referral program flyer for a top-tier restoration/remodel company. FILES I WILL PROVIDE I will send the designer: All replacement stock photos Any updated logos (if needed) Original high-resolution version of the mock-up (if available) Any additional icons preferred

```html
<!DOCTYPE html>
<html lang="en">
<head>
<meta charset="utf-8">
<title>Referral Program Flyer – Front and Back</title>
<link href="https://fonts.googleapis.com/css2?family=Poppins:wght@400;500;600;700;800;900&family=Oswald:wght@500;600;700&family=Bebas+Neue&display=swap" rel="stylesheet">
<style>
  :root{
    --navy:#173b80;
    --blue:#0054aa;
    --mid-blue:#0677ba;
    --sky:#7badd7;
    --pale:#cadeef;
    --mist:#e8f1f8;
    --yellow:#f7e21b;
    --white:#ffffff;
    --ink:#1b2030;
    --stage:#646468;
    --red:#d7252c;
  }
  *{box-sizing:border-box;margin:0;padding:0}
  html,body{width:1200px;height:2374px;overflow:hidden}
  body{background:var(--stage);font-family:"Poppins",sans-serif;position:relative}

  .card{position:absolute;left:152px;width:896px;height:579px;background:var(--white);overflow:hidden;box-shadow:0 18px 30px rgba(0,0,0,.35)}
  .card--front{top:131px}
  .card--back{top:841px}
  .abs{position:absolute}
  .shape-layer{position:absolute;inset:0}
  .ring{position:absolute;border-radius:50%}
  .photo{position:absolute;border-radius:50%;overflow:hidden}

  /* headline */
  .headline{position:absolute;left:296px;top:26px;display:flex;align-items:baseline;gap:10px;color:var(--navy);font-weight:800;white-space:nowrap}
  .headline__lead{font-size:40px;letter-spacing:-1px;color:var(--navy)}
  .headline__cash{font-size:68px;font-weight:900;letter-spacing:-1px;line-height:1}
  .tagline-band{position:absolute;left:332px;top:107px;width:564px;height:46px;background:var(--yellow);clip-path:polygon(22px 0,100% 0,100% 100%,0 100%)}
  .tagline-band span{position:absolute;right:22px;top:3px;font-size:31px;font-weight:800;color:var(--navy);white-space:nowrap;letter-spacing:-.3px}
  .partner-line{position:absolute;left:414px;width:460px;text-align:center;font-weight:800;font-size:42px;line-height:1;letter-spacing:-.3px;white-space:nowrap}
  .partner-line--one{top:176px;color:var(--navy)}
  .partner-line--two{top:231px;color:var(--blue)}

  /* benefits */
  .benefit{position:absolute;width:180px}
  .benefit__title{font-size:13.5px;font-weight:700;color:var(--blue);line-height:1.28;text-transform:uppercase}
  .benefit__text{margin-top:12px;width:165px;font-size:11.4px;color:var(--ink);line-height:1.3}
  .benefit__icon{position:absolute;left:108px;top:-4px;width:34px;height:34px;border-radius:50%;border:2px solid var(--yellow);background:var(--white);display:flex;align-items:center;justify-content:center}
  .benefit__icon svg{width:20px;height:20px}

  /* cash incentive */
  .incentive{position:absolute;left:0;top:361px;width:364px;height:50px;background:var(--blue);color:var(--white)}
  .incentive__amount{position:absolute;left:22px;top:3px;width:86px;text-align:center;font-size:30px;font-weight:800;line-height:1}
  .incentive__min{position:absolute;left:22px;top:33px;width:86px;text-align:center;font-size:11px;font-weight:700;color:var(--yellow)}
  .incentive__or{position:absolute;left:113px;top:-13px;width:74px;height:74px;border-radius:50%;background:var(--yellow);border:5px solid var(--white);display:flex;align-items:center;justify-content:center;font-family:"Oswald",sans-serif;font-weight:600;font-size:34px;color:var(--navy)}
  .incentive__pct{position:absolute;left:198px;top:0;font-family:"Oswald",sans-serif;font-size:42px;font-weight:500;line-height:1;color:var(--sky)}
  .incentive__per{position:absolute;left:270px;top:7px;font-size:13.5px;font-weight:700;color:var(--yellow);line-height:1.2}

  /* premier ribbon */
  .ribbon{position:absolute;left:63px;top:457px;width:241px;height:62px}
  .ribbon__top{position:absolute;left:0;top:0;width:241px;height:18px;background:var(--yellow);text-align:center;font-size:11.5px;font-weight:700;color:var(--blue);line-height:18px}
  .ribbon__bar{position:absolute;left:0;top:20px;width:241px;height:38px;background:var(--blue)}
  .ribbon__word{position:absolute;top:21px;font-family:"Oswald",sans-serif;font-size:22px;font-weight:500;color:var(--yellow);line-height:36px}
  .ribbon__badge{position:absolute;left:97px;top:16px;width:48px;height:48px;border-radius:50%;background:var(--yellow);border:3px solid var(--white);display:flex;align-items:center;justify-content:center}

  /* contact bar */
  .contact{position:absolute;left:0;bottom:0;width:896px;height:43px}
  .contact__call{position:absolute;left:0;top:0;width:590px;height:43px;background:var(--sky);clip-path:polygon(0 0,100% 0,94% 100%,0 100%)}
  .contact__web{position:absolute;right:0;top:0;width:330px;height:43px;background:var(--yellow);clip-path:polygon(14% 0,100% 0,100% 100%,0 100%)}
  .contact__label{position:absolute;left:50px;top:12px;font-size:16px;color:var(--navy);font-weight:500}
  .contact__phone{position:absolute;left:290px;top:2px;font-size:29px;font-weight:800;color:var(--navy);letter-spacing:.5px}
  .contact__url{position:absolute;right:18px;top:8px;font-size:19px;font-weight:700;color:var(--navy)}

  /* back: steps */
  .step{position:absolute;left:384px;width:286px;height:106px}
  .step__box{position:absolute;left:90px;top:7px;width:194px;height:91px;background:var(--yellow);border:2px solid var(--navy);border-radius:0 6px 6px 0}
  .step__photo{position:absolute;left:0;top:0;width:106px;height:106px;border-radius:50%;border:3px solid var(--navy)}
  .step__title{position:absolute;left:120px;top:14px;width:160px;font-size:12.5px;font-weight:700;color:var(--blue);line-height:1.3;text-transform:uppercase}
  .step__title--case{text-transform:none;font-size:13.5px}
  .step__text{position:absolute;left:120px;width:160px;font-size:11px;color:var(--ink);line-height:1.3}
  .emergency-seal{position:absolute;left:771px;top:22px;width:112px;height:112px;border-radius:50%;border:4px solid var(--red);background:var(--white)}
  .emergency-seal::after{content:"";position:absolute;inset:16px;border-radius:50%;background:var(--red)}

  .side-photo{position:absolute;border:3px solid var(--white);border-radius:4px;box-shadow:0 2px 6px rgba(0,0,0,.3)}

  .slogan{position:absolute;width:150px;font-family:"Bebas Neue",sans-serif;line-height:.9;text-transform:uppercase;white-space:nowrap}
  .slogan__small{display:block;font-size:33px;color:var(--white)}
  .slogan__big{display:block;font-size:80px;background:linear-gradient(180deg,#fff35a,#f5a21c);-webkit-background-clip:text;background-clip:text;color:transparent}
</style>
</head>
<body>

<!-- FRONT -->
<section class="card card--front" aria-label="Referral flyer front">
  <svg class="shape-layer" viewBox="0 0 896 579" preserveAspectRatio="none" aria-hidden="true">
    <polygon points="0,0 157,0 493,536 0,536" fill="#0054aa"/>
    <polygon points="0,0 157,0 250,150 0,250" fill="#173b80" opacity=".45"/>
    <polygon points="0,420 300,400 493,536 0,536" fill="#173b80" opacity=".6"/>
  </svg>
  <div class="ring" style="left:40px;top:74px;width:360px;height:360px;background:var(--white)"></div>
  <div class="ring" style="left:46px;top:80px;width:348px;height:348px;background:var(--blue)"></div>
  <div class="ring" style="left:74px;top:86px;width:346px;height:346px;background:var(--white)"></div>
  <div class="photo" role="img" aria-label="Photo of a flooded kitchen and dining room with water on the floor"
       style="left:84px;top:96px;width:326px;height:326px;background:radial-gradient(circle at 55% 35%,#e6e8ea,#8d939a 55%,#2e3440)"></div>

  <div class="headline"><span class="headline__lead">EARN UNLIMITED</span><span class="headline__cash">CASH</span></div>
  <div class="tagline-band"><span>GET PAID TOREFER A FLOOD</span></div>
  <div class="partner-line partner-line--one">PARTNER WITH US &amp;</div>
  <div class="partner-line partner-line--two">EVERYBODY WINS!</div>

  <div class="benefit" style="left:496px;top:319px">
    <div class="benefit__title">Guaranteed<br>Payout*</div>
    <div class="benefit__icon"><svg viewBox="0 0 24 24" fill="none" stroke="#173b80" stroke-width="2"><circle cx="12" cy="12" r="4"/><path d="M12 2v3M12 19v3M2 12h3M19 12h3M5 5l2 2M17 17l2 2M5 19l2-2M17 7l2-2"/></svg></div>
    <div class="benefit__text">Minimum $500 or 10% of Total Invoice Paid Fast</div>
  </div>
  <div class="benefit" style="left:700px;top:319px">
    <div class="benefit__title">Free<br>Estimates</div>
    <div class="benefit__icon"><svg viewBox="0 0 24 24" fill="none" stroke="#173b80" stroke-width="2"><rect x="5" y="3" width="14" height="18" rx="1"/><path d="M8 8h8M8 12h8M8 16h5"/></svg></div>
    <div class="benefit__text">Fast &amp; Free Inspections<br>&amp; Written Estimates</div>
  </div>
  <div class="benefit" style="left:496px;top:423px">
    <div class="benefit__title">Affordable<br>Solutions</div>
    <div class="benefit__icon"><svg viewBox="0 0 24 24" fill="none" stroke="#173b80" stroke-width="2"><circle cx="12" cy="8" r="5"/><path d="M3 20c3-3 6-3 9-2s5 0 9-3"/></svg></div>
    <div class="benefit__text">Lowest Out of Pocket<br>Costs for Your Customers</div>
  </div>
  <div class="benefit" style="left:700px;top:423px">
    <div class="benefit__title">Industry<br>Leaders</div>
    <div class="benefit__icon"><svg viewBox="0 0 24 24" fill="none" stroke="#173b80" stroke-width="2"><circle cx="12" cy="6" r="2.5"/><circle cx="6" cy="12" r="2.5"/><circle cx="18" cy="12" r="2.5"/><path d="M2 20c1-3 7-3 8 0M14 20c1-3 7-3 8 0M9 15c1-3 5-3 6 0"/></svg></div>
    <div class="benefit__text">Licensed &amp; Certified Experts Provide 100% Guarantee</div>
  </div>

  <div class="incentive">
    <div class="incentive__amount">$500</div>
    <div class="incentive__min">MINIMUM</div>
    <div class="incentive__or">OR</div>
    <div class="incentive__pct">10%</div>
    <div class="incentive__per">PER<br>REFERRAL</div>
  </div>

  <div class="ribbon">
    <div class="ribbon__top">PREMIER</div>
    <div class="ribbon__bar"></div>
    <div class="ribbon__word" style="left:10px">PARTNER</div>
    <div class="ribbon__word" style="right:6px">PROGRAM</div>
    <div class="ribbon__badge"><svg width="26" height="26" viewBox="0 0 24 24" fill="none" stroke="#173b80" stroke-width="3.4" stroke-linecap="round" stroke-linejoin="round"><path d="M4 12l5 5L20 6"/></svg></div>
  </div>

  <div class="contact">
    <div class="contact__call"></div>
    <div class="contact__web"></div>
    <div class="contact__label">CALL TEXT OR BOOK ONLINE</div>
    <div class="contact__phone">858-471-6093</div>
    <div class="contact__url">BRIGHTLANERENOVATE.COM</div>
  </div>
</section>

<!-- BACK -->
<section class="card card--back" aria-label="Referral flyer back">
  <svg class="shape-layer" viewBox="0 0 896 579" preserveAspectRatio="none" aria-hidden="true">
    <polygon points="0,0 157,0 484,536 0,536" fill="#0054aa"/>
    <polygon points="0,0 157,0 250,150 0,250" fill="#173b80" opacity=".45"/>
    <polygon points="0,400 330,380 484,536 0,536" fill="#173b80" opacity=".75"/>
  </svg>
  <div class="abs" role="img" aria-label="Photo of a city skyline across the water at dusk"
       style="left:355px;top:391px;width:541px;height:139px;clip-path:polygon(0 0,100% 0,100% 100%,24% 100%);background:linear-gradient(180deg,#7d6fa6 0%,#c58aa8 45%,#3a3552 75%,#2a3a5c 100%)"></div>

  <div class="ring" style="left:42px;top:76px;width:340px;height:340px;background:var(--white)"></div>
  <div class="ring" style="left:48px;top:82px;width:328px;height:328px;background:var(--blue)"></div>
  <div class="ring" style="left:72px;top:88px;width:322px;height:322px;background:var(--white)"></div>
  <div class="photo" role="img" aria-label="Photo of banknotes with letter tiles spelling cash flow"
       style="left:82px;top:98px;width:302px;height:302px;background:radial-gradient(circle at 50% 50%,#dfe3dc,#a9b0a6 60%,#6c736b)"></div>

  <div class="step" style="top:13px">
    <div class="step__box"></div>
    <div class="step__photo" role="img" aria-label="Photo of a house and a clipboard estimate" style="background:linear-gradient(160deg,#d9dde2,#7f9a6a)"></div>
    <div class="step__title">We Take Care of Everything:</div>
    <div class="step__text" style="top:52px">We Schedule a Free Estimate. If Approved, You Get Paid.</div>
  </div>
  <div class="step" style="top:142px">
    <div class="step__box"></div>
    <div class="step__photo" role="img" aria-label="Photo of a technician inspecting a ceiling" style="background:linear-gradient(160deg,#c9c3b8,#4e5968)"></div>
    <div class="step__title">Refer Flood, Mold &amp; Construction Jobs:</div>
    <div class="step__text" style="top:56px">It’s Simple to Refer 24/7: Call, Text or Book Online.</div>
  </div>
  <div class="step" style="top:270px">
    <div class="step__box"></div>
    <div class="step__photo" role="img" aria-label="Yellow road sign reading get paid to share" style="background:radial-gradient(circle,#f7e21b 45%,#a9c7e6 70%)"></div>
    <div class="step__title step__title--case">Everybody Benefits From Referrals</div>
    <div class="step__text" style="top:56px">We Provide Expert Quality Work for AAordable Price.v</div>
  </div>

  <div class="emergency-seal" aria-label="Emergency service seal"></div>

  <div class="side-photo" role="img" aria-label="Photo of drying fans and dehumidifiers in a room" style="left:697px;top:177px;width:184px;height:99px;background:linear-gradient(180deg,#e4e2de,#b7bfc5 60%,#3f86b8)"></div>
  <div class="side-photo" role="img" aria-label="Photo of a thermal camera scanning a room" style="left:736px;top:299px;width:106px;height:104px;background:linear-gradient(135deg,#efe9e1,#c2a57d 60%,#3b3b3b)"></div>

  <div class="slogan" style="left:44px;top:427px"><span class="slogan__small">The more you</span><span class="slogan__big">Refer</span></div>
  <div class="slogan" style="left:208px;top:419px"><span class="slogan__small">The more you</span><span class="slogan__big">Earn</span></div>

  <div class="contact">
    <div class="contact__call"></div>
    <div class="contact__web"></div>
    <div class="contact__label">CALL TEXT OR BOOK ONLINE</div>
    <div class="contact__phone">858-471-6093</div>
    <div class="contact__url">BRIGHTLANERENOVATE.COM</div>
  </div>
</section>

</body>
</html>
```